Bus tour company needs and new look for their brochure design

We already have a brochure designed using Printmorrow, but its very busy and we haven't had many tour booking from the brochures we have displayed out there.
Heart of the Kalvaro provides a variety of specialised tours that feature world class experiences that showcase the Fleurieu region’s (South Australia) culture, heritage, food and wine in an unspoilt natural environment. We would really like the brochure to have great images, some of which I have and some I dont. It needs to grab people attention when displayed amongst many others. We have a logo already and our bus has also been signed with the logo.
Our website is www.hkvoyages.com.au if you would like to have a look at what we do and how the site looks. I am not to fussed that the brochure look and feel the same as the website, just that it has a similar feel to the logo and our products we offer.

I would like to remove the Pendlebrook Run tour product from the brochure and add a different food and wine tour. I can provide this information when needed.
Updates

HI all designers I have added so logo images without the white background. Could you please try this logo option on your designs?

Target Market(s)

Activity Seekers – mix of young singles and older people (45+) often
travelling in groups of friends and more likely to be male.

The Indulge and Recharge Segment are more likely to be females aged
over 50 travelling with a partner or female friends.. They like
to indulge in little luxuries and special treats. great for regional food and wine tours.

Family Focussed – predominantly midlife families looking to spend quality
time and reconnect with partners and children.

Industry/Entity Type

It Company

Font styles to use
Serif
Sans Serif

Colors
3176b5
00a990
33a6d7
85cae6
000000
ffffff
9bcb3c
fbed22

Requirements
Must have
• Must have contact details; 0471 582 064
• book now www.hkvoyages.com.au
• great images
• logo
• reference to location: Fleurieu Peninsula, South Australia
Should not have
• too much detail in the products.

```html
<!DOCTYPE html>
<html lang="en">
<head>
<meta charset="utf-8">
<title>Heart of the Kalvaro Tours – Rack Cards</title>
<link rel="stylesheet" href="https://fonts.googleapis.com/css2?family=Oswald:wght@400;500;600&family=Pathway+Gothic+One&display=swap">
<style>
  :root{
    --brand-blue:#1f8fd6;
    --sky-blue:#33a6d7;
    --pale-blue:#85cae6;
    --deep-blue:#1674bd;
    --ink:#1a1a1a;
    --charcoal:#232323;
    --white:#ffffff;
    --mist:#eef0f2;
  }
  *{box-sizing:border-box;margin:0;padding:0}
  html,body{width:1200px;height:1200px;overflow:hidden;background:var(--white)}
  body{position:relative;font-family:"Pathway Gothic One",sans-serif;color:var(--ink)}

  .rack-card{position:absolute;top:132px;width:464px;height:954px;background:var(--white);overflow:hidden;box-shadow:0 3px 10px rgba(0,0,0,.25)}
  .rack-card--discover{left:105px}
  .rack-card--indulgence{left:633px}
  .card-bg{position:absolute;inset:0;width:464px;height:954px}

  .brand{position:absolute;left:20px;top:16px;font-family:"Oswald",sans-serif;font-weight:500;color:var(--ink);line-height:1;display:flex;align-items:center;gap:8px}
  .brand__name{font-size:30px;letter-spacing:.5px;text-transform:uppercase}
  .brand__name small{display:block;font-size:17px;letter-spacing:1px;margin-bottom:3px}
  .brand__dot{width:14px;height:14px;border-radius:50%;background:var(--brand-blue)}

  .photo{position:absolute;border-radius:50%;border:5px solid var(--white);box-shadow:0 0 0 5px var(--brand-blue)}
  .photo--arch{left:51px;top:112px;width:256px;height:256px;background:linear-gradient(180deg,#8a5a2c 0%,#c28a4c 18%,#5fa2dd 32%,#a9d3f2 55%,#3fb7b4 72%,#d9c8a4 100%)}
  .photo--picnic{left:273px;top:44px;width:184px;height:184px;background:radial-gradient(circle at 40% 60%,#e4d3b4 0%,#b08a60 45%,#4a3a2c 100%)}
  .photo--roo{left:257px;top:200px;width:152px;height:152px;background:radial-gradient(circle at 50% 55%,#9c8570 0%,#7d6a55 35%,#7ea24a 70%,#5d8a33 100%)}
  .photo--vineyard{left:203px;top:84px;width:232px;height:232px;background:linear-gradient(180deg,#2f7ed6 0%,#9ec9ee 38%,#6fae3a 52%,#3f8a22 100%)}
  .photo--plate{left:49px;top:143px;width:160px;height:160px;background:radial-gradient(circle at 50% 50%,#d96a4a 0%,#c8b46a 35%,#3fa5c8 75%,#2a86b0 100%)}
  .photo--wine{left:171px;top:224px;width:136px;height:136px;background:radial-gradient(circle at 50% 50%,#b21d22 0%,#7a1416 35%,#c4d85a 65%,#8fae2e 100%)}

  .title{position:absolute;left:26px;font-family:"Oswald",sans-serif;font-weight:500;font-size:26px;line-height:1;letter-spacing:-.3px;text-transform:uppercase}
  .subtitle{position:absolute;font-family:"Oswald",sans-serif;font-weight:500;font-size:17px;line-height:1;text-transform:uppercase}
  .intro{position:absolute;left:26px;right:22px;font-size:14px;line-height:17px}
  .bullets{position:absolute;list-style:none;font-size:14px;line-height:17px}
  .bullets li{position:relative;padding-left:8px;margin-bottom:3px}
  .bullets li::before{content:"";position:absolute;left:0;top:7px;width:3px;height:3px;border-radius:50%;background:currentColor}
  .bullets--blue li::before{background:var(--sky-blue)}

  .discover .title{top:398px;color:var(--ink)}
  .discover .intro{top:429px;color:var(--white)}
  .discover .subtitle.inc{left:26px;top:484px;color:var(--ink)}
  .discover .col-a{left:26px;top:504px;width:180px;color:var(--white)}
  .discover .col-b{left:267px;top:504px;width:170px;color:var(--white)}
  .discover .departs{position:absolute;left:33px;top:600px;font-size:14px;color:var(--white)}
  .discover .subtitle.hl{left:24px;top:662px;color:var(--brand-blue);font-size:18px;font-weight:400}
  .discover .highlights{left:26px;top:688px;width:420px;font-size:14px;line-height:18.5px;color:var(--ink)}
  .discover .highlights li{margin-bottom:0}

  .indulgence .title{top:388px;color:var(--sky-blue)}
  .indulgence .intro{top:421px;color:var(--white)}
  .indulgence .subtitle.inc{left:27px;top:492px;color:var(--sky-blue)}
  .indulgence .col-a{left:27px;top:514px;width:200px;color:var(--white)}
  .indulgence .col-b{left:252px;top:515px;width:190px;color:var(--white)}
  .indulgence .subtitle.hl{left:25px;top:710px;color:var(--brand-blue);font-size:18px;font-weight:400}
  .indulgence .highlights{left:27px;top:734px;width:420px;color:var(--ink)}
  .indulgence .highlights li{margin-bottom:2px}

  .phone{position:absolute;font-family:"Oswald",sans-serif;font-weight:500;color:var(--white);display:flex;align-items:center;gap:6px;line-height:1}
  .phone svg{width:18px;height:18px}
  .discover .phone{left:40px;top:856px;font-size:26px;color:var(--ink)}
  .discover .phone svg{fill:var(--brand-blue)}
  .discover .book{position:absolute;left:23px;top:902px;font-family:"Oswald",sans-serif;font-weight:500;font-size:22px;line-height:1.1;color:var(--sky-blue)}
  .discover .url{position:absolute;left:22px;top:930px;font-family:"Oswald",sans-serif;font-size:13px;line-height:1.1;color:var(--white)}

  .indulgence .phone{left:46px;top:856px;font-size:25px}
  .indulgence .phone svg{fill:var(--white)}
  .indulgence .book{position:absolute;left:24px;width:190px;text-align:center;top:884px;font-family:"Oswald",sans-serif;font-weight:500;font-size:19px;line-height:1;color:var(--ink)}
  .indulgence .url{position:absolute;left:24px;width:190px;text-align:center;top:908px;font-family:"Oswald",sans-serif;font-weight:500;font-size:13px;line-height:1;color:var(--white)}

  .tour-bus{position:absolute;border-radius:14px 22px 8px 8px;background:linear-gradient(180deg,#e9edf1 0%,#ffffff 45%,#c9cfd5 100%);box-shadow:0 2px 4px rgba(0,0,0,.3)}
  .discover .tour-bus{left:245px;top:854px;width:205px;height:86px}
  .indulgence .tour-bus{left:241px;top:846px;width:205px;height:84px}
</style>
</head>
<body>

<section class="rack-card rack-card--discover discover">
  <svg class="card-bg" viewBox="0 0 464 954" aria-hidden="true">
    <defs>
      <linearGradient id="blueWave" x1="0" y1="0" x2="1" y2="0">
        <stop offset="0" stop-color="#1674bd"/>
        <stop offset=".55" stop-color="#33a6d7"/>
        <stop offset="1" stop-color="#6cc6ef"/>
      </linearGradient>
      <linearGradient id="mistFade" x1="0" y1="0" x2="0" y2="1">
        <stop offset="0" stop-color="#ffffff"/>
        <stop offset="1" stop-color="#e8eaec"/>
      </linearGradient>
    </defs>
    <rect width="464" height="954" fill="#fff"/>
    <path d="M0 236 C40 300 120 360 240 378 C330 390 400 372 464 356 L464 640 C380 610 300 606 200 624 C120 636 50 640 0 626 Z" fill="url(#blueWave)"/>
    <path d="M0 236 C40 300 120 360 240 378 C330 390 400 372 464 356 L464 350 C400 364 330 382 240 370 C120 352 40 294 0 226 Z" fill="#1a1a1a"/>
    <path d="M0 626 C50 640 120 636 200 624 C300 606 380 610 464 640 L464 954 L0 954 Z" fill="url(#mistFade)"/>
    <path d="M0 626 C60 636 130 630 210 618 C300 604 390 612 464 646 L464 660 C390 624 300 616 212 630 C130 642 60 644 0 638 Z" fill="#1a1a1a"/>
    <path d="M0 894 C120 888 220 892 300 904 L464 920 L464 954 L0 954 Z" fill="#1a1a1a"/>
    <path d="M26 848 Q26 835 40 834 L230 834 Q232 870 234 898 C170 890 90 886 26 890 Z" fill="url(#blueWave)"/>
  </svg>

  <div class="brand">
    <div class="brand__name"><small>Heart of the</small>Kalvaro Tours</div>
    <span class="brand__dot"></span>
  </div>

  <div class="photo photo--arch" role="img" aria-label="Sea cave arch framing blue sky and turquoise ocean"></div>
  <div class="photo photo--picnic" role="img" aria-label="Gourmet picnic spread with bread, cheese and a bottle of red wine"></div>
  <div class="photo photo--roo" role="img" aria-label="Kangaroo in green grass"></div>

  <h1 class="title">Discover the Fleurieu</h1>
  <p class="intro">Enjoy a full day ultimate tour of the Fleurieu Peninsula. Perfect if you want to experience the best of nature and learn about the rich history of the region. Embrace yourself in unspoilt areas that allow you to truly become one with nature.</p>

  <h2 class="subtitle inc">Tour includes:</h2>
  <ul class="bullets col-a">
    <li>All park entrance fees</li>
    <li>All meals including morning tea, gourmet picnic lunch &amp; drinks</li>
    <li>Local wine tasting</li>
    <li>Professional &amp; friendly guide/driver</li>
  </ul>
  <p class="departs">Departs 8:00am (approx)</p>
  <ul class="bullets col-b">
    <li>Returns 5.00pm (approx)</li>
    <li>Minimum 2 people, family rates available</li>
    <li>Pick up and return from selected accommodation is available at no extra cost</li>
  </ul>

  <h2 class="subtitle hl">Highlights</h2>
  <ul class="bullets bullets--blue highlights">
    <li>An important South Australian landmark in Rapid Bay</li>
    <li>A guided walk through Deep Creek Conservation Park. The largest remaining block of wildlife habitat on the Fleurieu Peninsula</li>
    <li>Enjoy a gourmet picnic lunch besides some local kangaroos and bird-life before visiting the historic seaside town of Victor Harbor where you will discover some of the local Indigenous heritage, early settlement and whaling history.</li>
    <li>Enjoy some great photo opportunities of Encounter Bay, the Bluff and Granite Island.</li>
    <li>Then wind down with a glass of wine and gourmet cheese platter and at local winery.</li>
  </ul>

  <div class="phone">
    <svg viewBox="0 0 24 24" aria-hidden="true"><rect x="1" y="1" width="22" height="22" rx="5"/><path d="M8 5c1 0 2 3 2 4s-1 1-1 2 2 4 3 4 1-1 2-1 4 1 4 2-1 3-3 3C9 19 5 14 5 9c0-2 2-4 3-4z" fill="#fff"/></svg>
    <span>0471 582 064</span>
  </div>
  <div class="book">BOOK NOW</div>
  <div class="url">www.hkvoyages.com.au</div>
  <div class="tour-bus" role="img" aria-label="White tour minibus carrying the company name"></div>
</section>

<section class="rack-card rack-card--indulgence indulgence">
  <svg class="card-bg" viewBox="0 0 464 954" aria-hidden="true">
    <defs>
      <linearGradient id="pillBlue" x1="0" y1="0" x2="1" y2="0">
        <stop offset="0" stop-color="#1674bd"/>
        <stop offset="1" stop-color="#33a6d7"/>
      </linearGradient>
      <linearGradient id="mistFade2" x1="0" y1="0" x2="0" y2="1">
        <stop offset="0" stop-color="#ffffff"/>
        <stop offset="1" stop-color="#e8eaec"/>
      </linearGradient>
    </defs>
    <rect width="464" height="954" fill="#fff"/>
    <path d="M0 362 C100 350 200 352 290 340 C380 326 430 290 464 248 L464 690 C390 668 300 660 220 670 C130 682 60 686 0 680 Z" fill="#1e1e1e"/>
    <path d="M0 338 C100 330 200 334 290 322 C380 308 430 272 464 228 L464 248 C430 290 380 326 290 340 C200 352 100 350 0 362 Z" fill="#1f8fd6"/>
    <path d="M0 680 C60 686 130 682 220 670 C300 660 390 668 464 690 L464 954 L0 954 Z" fill="url(#mistFade2)"/>
    <path d="M0 672 C70 680 140 672 220 660 C300 650 390 660 464 690 L464 704 C390 676 300 668 222 678 C140 690 70 694 0 690 Z" fill="#1f8fd6"/>
    <path d="M0 938 C120 936 240 932 464 930 L464 954 L0 954 Z" fill="#1e1e1e"/>
    <path d="M24 864 Q24 851 38 851 L214 851 L214 930 C150 932 80 936 24 940 Z" fill="url(#pillBlue)"/>
  </svg>

  <div class="brand">
    <div class="brand__name"><small>Heart of the</small>Kalvaro Tours</div>
    <span class="brand__dot"></span>
  </div>

  <div class="photo photo--vineyard" role="img" aria-label="Rows of green vineyard under a blue sky"></div>
  <div class="photo photo--plate" role="img" aria-label="Fresh gourmet salad plate"></div>
  <div class="photo photo--wine" role="img" aria-label="Red wine pouring into a glass against green vines"></div>

  <h1 class="title">McLaren Vale Indulgence</h1>
  <p class="intro">The Fleurieu Peninsula has some of Australia’s tastiest food, wine and beer. This tour brings you the best of the McLaren Vale Wine Region. Enjoy a perfect day out in McLaren Vale, treat yourself to a fabulous day of exclusive tastings and experiences as you are collected from your accommodation and taken on a full-day private tour.</p>

  <h2 class="subtitle inc">Tour includes:</h2>
  <ul class="bullets bullets--blue col-a">
    <li>A private small group tour provides an intimate experience and ensures personal attention from your guide.</li>
    <li>All winery tasting fees</li>
    <li>Gourmet lunch</li>
    <li>Meet a local wine maker and viticulturist (subject to availability)</li>
    <li>Professional &amp; friendly guide/driver</li>
  </ul>
  <ul class="bullets bullets--blue col-b">
    <li>Pick up and return from selected accommodation is available at no extra cost</li>
    <li>Departs 9:00am</li>
    <li>Returns 5:00pm</li>
    <li>Minimum 2, Max 6 people (larger group tours available on request)</li>
  </ul>

  <h2 class="subtitle hl">Highlights</h2>
  <ul class="bullets bullets--blue highlights">
    <li>Gourmet local produce</li>
    <li>Boutique winery and brewery tasting</li>
    <li>Small-group tour limited to 6 people provides an intimate experience and ensures personal attention from your guide</li>
    <li>All tours are delivered with passion, integrity and style</li>
    <li>Travel in air-conditioned mini buses with experienced driver/guide</li>
  </ul>

  <div class="phone">
    <svg viewBox="0 0 24 24" aria-hidden="true"><path d="M7 2c1.5 0 3 4 3 5.5S8.5 9 8.5 10.5s3 5 4.5 5 1.5-1.5 3-1.5 5.5 1.5 5.5 3-1.5 4-4.5 4C9 21 3 14 3 7c0-3 2.5-5 4-5z"/></svg>
    <span>0471 582 064</span>
  </div>
  <div class="book">BOOK NOW</div>
  <div class="url">www.hkvoyages.com.au</div>
  <div class="tour-bus" role="img" aria-label="White tour minibus carrying the company name"></div>
</section>

</body>
</html>
```